Stonebridge Building and Projects business cards

A business card with watermark background (construction work)

Company logo attached

Home improvement projects
House renovations
Bathroom and kitchen renovations
House extensions
New builds and granny flats

Director Omar Haddani
(Phone number)
omar@sbpbuilding.com.au
(Instagram logo) sbp_building

```html
<!DOCTYPE html>
<html lang="en">
<head>
<meta charset="utf-8">
<title>Stonebridge Building and Projects – Business Cards</title>
<link rel="stylesheet" href="https://fonts.googleapis.com/css2?family=Roboto:wght@400;500&display=swap">
<style>
  :root {
    --brand-blue: #3377bb;
    --card-blue: #3577b5;
    --ink: #3a3a3a;
    --charcoal: #262626;
    --paper: #ffffff;
    --backdrop: #e9eaec;
    --rule: #c9c9c9;
  }
  * { box-sizing: border-box; margin: 0; padding: 0; }
  html, body {
    width: 1200px; height: 1200px; overflow: hidden;
    background: var(--backdrop);
    font-family: "Roboto", Arial, sans-serif;
  }
  .card {
    position: absolute; left: 257px;
    width: 686px; height: 392px;
    box-shadow: 0 18px 30px rgba(0,0,0,0.18);
  }
  .card--front { top: 165px; background: var(--paper); }
  .card--back { top: 653px; background: var(--card-blue); }

  .wordmark {
    position: absolute; left: 40px; top: 150px; width: 230px;
    text-align: center; font-weight: 500; line-height: 1.15;
  }
  .wordmark__mark {
    display: block; width: 14px; height: 14px; margin: 0 auto 8px;
    background: currentColor;
  }
  .wordmark__name { display: block; font-size: 27px; }
  .wordmark__sub { display: block; font-size: 15px; letter-spacing: 0.5px; }
  .card--front .wordmark { color: var(--brand-blue); }
  .card--back .wordmark { color: var(--paper); }

  .divider { position: absolute; width: 1px; }
  .card--front .divider { left: 309px; top: 132px; height: 130px; background: var(--rule); }
  .card--back .divider { left: 296px; top: 134px; height: 124px; background: rgba(255,255,255,0.8); }

  .person { position: absolute; left: 337px; top: 131px; }
  .person__name { font-size: 25px; font-weight: 500; color: var(--brand-blue); line-height: 1.2; }
  .person__role { font-size: 15.5px; font-weight: 500; color: var(--ink); margin-top: 1px; }

  .contacts { position: absolute; left: 337px; top: 197px; list-style: none; }
  .contacts li {
    display: flex; align-items: center; gap: 9px;
    font-size: 15.5px; color: var(--ink); height: 20px;
  }
  .contacts svg { width: 13px; height: 13px; fill: var(--brand-blue); flex: none; }

  .web-band {
    position: absolute; left: 0; top: 334px; width: 597px; height: 29px;
    background: var(--brand-blue); color: var(--paper);
    font-size: 15.5px; letter-spacing: 3.6px;
    display: flex; align-items: center; justify-content: center;
  }
  .web-band__end {
    position: absolute; left: 599px; top: 334px; width: 87px; height: 29px;
    background: var(--charcoal);
  }

  .services {
    position: absolute; left: 327px; top: 126px; list-style: none;
  }
  .services li {
    display: flex; align-items: center; gap: 11px;
    font-size: 16.5px; color: var(--paper); height: 25px;
  }
  .services svg { width: 9px; height: 9px; fill: var(--paper); flex: none; }
</style>
</head>
<body>

<section class="card card--front">
  <div class="wordmark">
    <span class="wordmark__mark"></span>
    <span class="wordmark__name">Stonebridge</span>
    <span class="wordmark__sub">Building and Projects</span>
  </div>
  <div class="divider"></div>
  <div class="person">
    <p class="person__name">Omar Haddani</p>
    <p class="person__role">Director</p>
  </div>
  <ul class="contacts">
    <li>
      <svg viewBox="0 0 24 24" aria-hidden="true"><path d="M6.6 10.8c1.4 2.8 3.8 5.1 6.6 6.6l2.2-2.2c.3-.3.7-.4 1-.2 1.1.4 2.3.6 3.6.6.6 0 1 .4 1 1V20c0 .6-.4 1-1 1C10.6 21 3 13.4 3 4c0-.6.4-1 1-1h3.5c.6 0 1 .4 1 1 0 1.3.2 2.5.6 3.6.1.3 0 .7-.2 1L6.6 10.8z"/></svg>
      555-014-2387
    </li>
    <li>
      <svg viewBox="0 0 24 24" aria-hidden="true"><path d="M2 5h20v14H2z M3.5 6.5 12 12.5l8.5-6" /><path d="M2 5h20v2l-10 6.5L2 7z" fill="#fff" opacity="0.6"/></svg>
      omar@sbpbuilding.com.au
    </li>
    <li>
      <svg viewBox="0 0 24 24" aria-hidden="true"><circle cx="12" cy="12" r="11"/></svg>
      sbp_building
    </li>
  </ul>
  <div class="web-band">www.sbpbuilding.com.au</div>
  <div class="web-band__end"></div>
</section>

<section class="card card--back">
  <div class="wordmark">
    <span class="wordmark__mark"></span>
    <span class="wordmark__name">Stonebridge</span>
    <span class="wordmark__sub">Building and Projects</span>
  </div>
  <div class="divider"></div>
  <ul class="services">
    <li><svg viewBox="0 0 9 9" aria-hidden="true"><rect width="3.5" height="3.5"/><rect x="5.5" width="3.5" height="3.5"/><rect y="5.5" width="3.5" height="3.5"/><rect x="5.5" y="5.5" width="3.5" height="3.5"/></svg>Home improvement projects</li>
    <li><svg viewBox="0 0 9 9" aria-hidden="true"><rect width="3.5" height="3.5"/><rect x="5.5" width="3.5" height="3.5"/><rect y="5.5" width="3.5" height="3.5"/><rect x="5.5" y="5.5" width="3.5" height="3.5"/></svg>House renovations</li>
    <li><svg viewBox="0 0 9 9" aria-hidden="true"><rect width="3.5" height="3.5"/><rect x="5.5" width="3.5" height="3.5"/><rect y="5.5" width="3.5" height="3.5"/><rect x="5.5" y="5.5" width="3.5" height="3.5"/></svg>Bathroom &amp; kitchen renovations</li>
    <li><svg viewBox="0 0 9 9" aria-hidden="true"><rect width="3.5" height="3.5"/><rect x="5.5" width="3.5" height="3.5"/><rect y="5.5" width="3.5" height="3.5"/><rect x="5.5" y="5.5" width="3.5" height="3.5"/></svg>House extensions</li>
    <li><svg viewBox="0 0 9 9" aria-hidden="true"><rect width="3.5" height="3.5"/><rect x="5.5" width="3.5" height="3.5"/><rect y="5.5" width="3.5" height="3.5"/><rect x="5.5" y="5.5" width="3.5" height="3.5"/></svg>New builds &amp; granny flats</li>
  </ul>
</section>

</body>
</html>
```